Established research company needs fresh new powerpoint template

We need a powerpoint template for an established research and advisory company called Quenlow Partnership. We develop policy, improve delivery, and build capacity within the public sector - mainly in relation to education and young people.

We have a long and successful track record in our sector, and have a grown-up, clean brand. We already have a logo (see attached) and want a simple, clean powerpoint template that incorporates our logo and colours and matches the brand identity on our website: https://www.quenlowpartnership.com/

We need a title slide, a section header slide, a two-column slide for two panels of text, a two-column slide for one panel of text and one panel of imagery, and a single-column slide for text.

We want a template with built-in Styles so our team can make consistent-looking presentations without any manual formatting. We also want to use a font that will be compatible with devices used across a range of clients.

```html
<!DOCTYPE html>
<html lang="en">
<head>
<meta charset="utf-8">
<title>Quenlow Partnership – Presentation Template</title>
<link rel="stylesheet" href="https://fonts.googleapis.com/css2?family=Lato:ital,wght@0,400;0,700;1,400;1,700&display=swap">
<style>
:root{
  --orange:#f07f3a;
  --grey:#8c92a0;
  --ink:#474a52;
  --page:#3a3a3a;
  --white:#ffffff;
  --rule:#e2e4e8;
}
*{box-sizing:border-box;margin:0;padding:0}
html,body{width:1200px;height:4135px;overflow:hidden;background:var(--page);font-family:"Lato",Arial,sans-serif;color:var(--ink)}
.slide{position:absolute;left:61px;width:1097px;height:614px;background:var(--white);overflow:hidden}
.slide::after{content:"";position:absolute;left:0;right:0;bottom:0;height:6px;background:linear-gradient(90deg,var(--orange) 0 568px,var(--grey) 568px 100%)}
.brand{position:absolute;font-weight:700;color:var(--grey);line-height:.82;letter-spacing:-.5px;display:flex;align-items:flex-start;gap:6px}
.brand .dot{display:block;background:var(--orange)}
.brand-sm{font-size:25px}
.brand-sm .dot{width:9px;height:9px;margin-top:2px}
.slide-title{position:absolute;left:55px;top:55px;font-size:38px;font-weight:400;color:var(--grey);letter-spacing:-.3px}
.slide-title em,.accent{font-style:normal;color:var(--orange)}
.marker{position:absolute;left:0;top:64px;width:23px;height:29px;background:var(--orange)}
.date{position:absolute;left:53px;bottom:26px;font-size:13px;font-weight:700;color:var(--orange)}
.page-no{position:absolute;right:55px;bottom:26px;font-size:13px;color:var(--grey)}
.body{font-size:12.6px;line-height:28px;color:var(--ink)}
.photo{position:absolute}
/* cover */
.cover .photo{left:0;top:0;width:1097px;height:457px;background:linear-gradient(100deg,#d9c3ae 0%,#b9a38f 30%,#e9e4dc 55%,#8a5d43 75%,#c9d3df 100%)}
.cover .brand{left:53px;top:494px;font-size:60px}
.cover .brand .dot{width:16px;height:16px;margin-top:4px}
.contact-row{position:absolute;left:746px;display:flex;align-items:center;gap:12px;font-size:15.5px;font-weight:700;color:var(--orange)}
/* welcome */
.welcome-title{position:absolute;left:0;right:0;top:56px;text-align:center;font-size:35px;color:var(--grey)}
.hero-box{position:absolute;left:164px;top:157px;width:771px;height:301px;background:var(--orange);border-radius:14px;color:var(--white);text-align:center;padding:52px 50px 0}
.hero-kicker{font-size:15.5px;letter-spacing:.2px}
.hero-head{font-size:34px;font-weight:700;line-height:48px;margin-top:14px}
.hero-sub{font-size:12px;line-height:28px;margin-top:12px;font-weight:700}
.foot-brand{left:53px;top:545px}
/* two column */
.col{position:absolute;top:126px;width:452px;text-align:justify}
.col p+p{margin-top:28px}
.col-divider{position:absolute;left:548px;top:126px;width:1px;height:380px;background:var(--rule)}
.head-brand{right:55px;top:55px}
/* research */
.research .photo{left:55px;top:133px;width:330px;height:374px;border-radius:14px;background:linear-gradient(160deg,#3c4452 0%,#6d5a48 45%,#b38a68 70%,#2d3440 100%)}
.research-sub{position:absolute;left:452px;top:130px;font-size:16px;color:var(--ink)}
.quote{position:absolute;left:385px;top:178px;width:658px;height:172px;background:var(--orange);color:var(--white);padding:18px 40px 0 68px;font-size:12.6px;line-height:27.5px;font-weight:700}
.quote cite{display:block;font-style:italic}
.research .body{position:absolute;left:452px;top:378px;width:590px}
/* join */
.join .body{position:absolute;left:55px;top:124px;width:990px;line-height:27px}
.join p{margin-bottom:9px}
.ticks{list-style:none;margin:4px 0 13px}
.ticks li{display:flex;align-items:center;gap:9px;margin-bottom:10px}
/* contact */
.reg{position:absolute;left:55px;top:127px;font-size:14.5px;line-height:34px}
.info{position:absolute;left:55px;display:flex;gap:12px}
.info .icon{width:40px;height:40px;border-radius:50%;background:var(--grey);display:flex;align-items:center;justify-content:center;margin-top:12px}
.info h3{font-size:18.5px;font-weight:400;color:var(--orange);line-height:28px}
.info p{font-size:14.5px;line-height:28px;color:#222}
.contact-divider{position:absolute;left:548px;top:128px;width:1px;height:370px;background:var(--rule)}
.thanks{position:absolute;left:629px;top:232px;font-size:40px;font-weight:700;color:var(--orange)}
.contact .big-brand{left:629px;top:300px;font-size:62px}
.contact .big-brand .dot{width:16px;height:16px;margin-top:4px}
</style>
</head>
<body>

<!-- Title slide -->
<section class="slide cover" style="top:48px">
  <div class="photo" role="img" aria-label="Photo of colleagues smiling around a meeting table reviewing documents"></div>
  <div class="brand"><span>quenlow<br>partnership</span><span class="dot"></span></div>
  <div class="contact-row" style="top:507px">
    <svg width="20" height="20" viewBox="0 0 20 20"><rect width="20" height="20" rx="4" fill="#f07f3a"/><path d="M6 4.5l2 .2 1 3-1.3 1a7 7 0 003.6 3.6l1-1.3 3 1 .2 2c-.3 1-1.2 1.5-2.3 1.3A10 10 0 014.7 6.8C4.5 5.7 5 4.8 6 4.5z" fill="#fff"/></svg>
    <span>Call Now: +1 555 010 0188</span>
  </div>
  <div class="contact-row" style="top:546px">
    <svg width="20" height="20" viewBox="0 0 20 20"><rect width="20" height="20" rx="4" fill="#f07f3a"/><rect x="4.5" y="6" width="11" height="8" rx="1" fill="#fff"/><path d="M5 6.8l5 3.6 5-3.6" stroke="#f07f3a" stroke-width="1.2" fill="none"/></svg>
    <span>Mail Us: info@quenlowpartnership.com</span>
  </div>
</section>

<!-- Section header -->
<section class="slide welcome" style="top:730px">
  <h1 class="welcome-title">Welcome to <span class="accent">quenlow</span> partnership</h1>
  <div class="hero-box">
    <p class="hero-kicker">BETTER PUBLIC SERVICES</p>
    <h2 class="hero-head">We help the public sector solve problems and deliver effectively.</h2>
    <p class="hero-sub">We are a research and advisory company with a track-record in developing policy, improving delivery, and building capacity within the public sector.</p>
  </div>
  <div class="brand brand-sm foot-brand"><span>quenlow<br>partnership</span><span class="dot"></span></div>
  <span class="page-no">Page No: 02</span>
</section>

<!-- Two text columns -->
<section class="slide about" style="top:1408px">
  <span class="marker"></span>
  <h1 class="slide-title">About <em>quenlow</em> partnership</h1>
  <div class="brand brand-sm head-brand"><span>quenlow<br>partnership</span><span class="dot"></span></div>
  <div class="col body" style="left:55px">
    <p>We have in-depth experience of working with the public sector, in the UK and overseas, in education, local government, health and social care. We have expertise and a proven track record in developing policy and strategy, solving delivery problems, undertaking national evaluations and writing influential research reports, advising on organisational reform, and facilitating workshops and conferences.</p>
    <p>On many of our projects, we work with our expert research partners. They have an array of experience in carrying out research and delivering improvements in public services, and they bring a wide range of skills and expertise to our work. We can support you to develop policies and strategies and design performance and delivery systems to implement these. We have a strong record in engaging stakeholders in designing systems and strategic planning.</p>
  </div>
  <span class="col-divider"></span>
  <div class="col body" style="left:594px">
    <p>We can assess and strengthen programme implementation, review progress of established projects, and provide rapid feedback from delivery partners. We can also work with you to reconfigure services and resources to maximise value for money. We will transfer skills and knowledge in every project we undertake. In addition we can work with you to create dedicated performance and delivery capability within your organization. We coach and train top teams and facilitate partner and stakeholder workshops.</p>
    <p>We are skilled in evaluating the impact of policies, using both qualitative and quantitative techniques, and can undertake bespoke research projects to inform policy making and delivery.There has been significant focus on support for young people with high needs recently.</p>
  </div>
  <span class="date">15 Dec 2023</span>
  <span class="page-no">Page No: 03</span>
</section>

<!-- Text and image -->
<section class="slide research" style="top:2100px">
  <span class="marker"></span>
  <h1 class="slide-title"><em>Research</em> and evaluation</h1>
  <div class="brand brand-sm head-brand"><span>quenlow<br>partnership</span><span class="dot"></span></div>
  <div class="photo" role="img" aria-label="Photo of two professionals in conversation at a meeting table"></div>
  <p class="research-sub">Research into the pressures on SEND and high needs budgets</p>
  <blockquote class="quote">‘Have we reached a “tipping point”? Trends in spending for children and young people with SEND in England provided a powerful and concise picture of the high needs budgetary and demand pressures facing member councils.’
    <cite>— Councillor Maren Holloway, Chair of the RCA’s Children and Young People Board</cite></blockquote>
  <p class="body">There has been significant focus on support for young people with high needs recently. This has been prompted by the reforms of the framework for supporting young people with special educational needs and disability (SEND), rising rates of exclusions and placements in alternative provision (AP), and rising pressure on resources for young people with additional and high needs.</p>
  <span class="date">15 Dec 2023</span>
  <span class="page-no">Page No: 04</span>
</section>

<!-- Single column -->
<section class="slide join" style="top:2783px">
  <span class="marker"></span>
  <h1 class="slide-title"><em>Join</em> our team</h1>
  <div class="brand brand-sm head-brand"><span>quenlow<br>partnership</span><span class="dot"></span></div>
  <div class="body">
    <p>We are always interested in talking to dynamic, talented people who share our values and commitment to working with the public sector to build capacity, improve delivery, and achieve better outcomes.</p>
    <p>The skills we look for in people to join our team at Quenlow Partnership are:</p>
    <ul class="ticks">
      <li><svg width="12" height="10" viewBox="0 0 12 10"><path d="M1 5l3.5 3.5L11 1.5" stroke="#f07f3a" stroke-width="2.2" fill="none"/></svg>Excellent communication skills, both written and oral; outstanding strategic-thinking, analytical, and problem-solving abilities;</li>
      <li><svg width="12" height="10" viewBox="0 0 12 10"><path d="M1 5l3.5 3.5L11 1.5" stroke="#f07f3a" stroke-width="2.2" fill="none"/></svg>Qualitative and quantitative research skills; the ability to work with and influence senior stakeholders; and</li>
      <li><svg width="12" height="10" viewBox="0 0 12 10"><path d="M1 5l3.5 3.5L11 1.5" stroke="#f07f3a" stroke-width="2.2" fill="none"/></svg>Expertise and a track-record of success in a specific area of the public sector – such as education, special educational needs, mental health, or children’s services.</li>
    </ul>
    <p>There are a range of ways in you could work with us, ranging from joining our team as a permanent employee to working with us as one of our expert associates. We are interested in hearing from people at the start of their careers, with at least two years of experience, as well as those with much more experience in their field. Please do get in touch with us at info@quenlowpartnership.com. We look forward to hearing from you. We have in-depth experience of working with the public sector, in the UK and overseas, in education, local government, health and social care. We have expertise and a proven track record in developing policy and strategy, solving delivery problems, undertaking national evaluations and writing influential research reports, advising on organisational reform, and facilitating workshops and conferences.</p>
  </div>
  <span class="date">15 Dec 2023</span>
  <span class="page-no">Page No: 05</span>
</section>

<!-- Contact -->
<section class="slide contact" style="top:3453px">
  <span class="marker"></span>
  <h1 class="slide-title"><em>Get</em> in touch with us</h1>
  <p class="reg">Partnership No: OC517204 | VAT No: 471 2259 36<br>‘Quenlow Partnership’ is the trading name of Quenlow<br>Partnership (UK) LLP</p>
  <div class="info" style="top:264px">
    <span class="icon"><svg width="14" height="18" viewBox="0 0 14 18"><path d="M7 1a6 6 0 00-6 6c0 4.5 6 10 6 10s6-5.5 6-10a6 6 0 00-6-6z" fill="#fff"/><circle cx="7" cy="7" r="2.2" fill="#8c92a0"/></svg></span>
    <div><h3>Address:</h3><p>41 Harlow Lane, London, N4 2QT</p></div>
  </div>
  <div class="info" style="top:364px">
    <span class="icon"><svg width="16" height="12" viewBox="0 0 16 12"><rect x="1" y="1" width="14" height="10" rx="1" fill="#fff"/><path d="M1.5 1.8L8 6.5l6.5-4.7" stroke="#8c92a0" stroke-width="1.3" fill="none"/></svg></span>
    <div><h3>Email Us:</h3><p>info@quenlowpartnership.com</p></div>
  </div>
  <div class="info" style="top:462px">
    <span class="icon"><svg width="16" height="16" viewBox="0 0 20 20"><path d="M6 3l2.3.3 1.1 3.4-1.5 1.1a8 8 0 004.2 4.2l1.1-1.5 3.4 1.1.3 2.3c-.3 1.2-1.4 1.8-2.7 1.6A11.5 11.5 0 014.4 5.7C4.2 4.4 4.8 3.3 6 3z" fill="#fff"/></svg></span>
    <div><h3>Phone Number:</h3><p>+1 555 010 0188</p></div>
  </div>
  <span class="contact-divider"></span>
  <p class="thanks">Thank You</p>
  <div class="brand big-brand"><span>quenlow<br>partnership</span><span class="dot"></span></div>
  <span class="date">15 Dec 2023</span>
  <span class="page-no">Page No: 06</span>
</section>

</body>
</html>
```